Trailer Lettering or Partial Wrap

I purchased a new gloss black 7' wide x 12' long x 7' height enclosed cargo trailer that I would like to brand for advertising. on all 4 sides. Our font is AgencyFB (and we only use lower case letters). To reduce cost I thought using the black gloss background could be achieved and use cut out vinyl rather than full wrap unless there are some other ideas. Our colors are Black, White, and Red (HEX #BE1E2D. Items to be displayed:
- logo
- phone # (405) 555-2716
- email. catering@kelpcornerok.com
- web address: www.kelpcornerok.com
- our 2 restaurant locations
- "Edmond" 4875 NE 92nd, Edmond OK 73099
- "NW-OKC" 2719 E Larkspur Ave, Oklahoma City, OK 73198

we would also like to highlight 3 services we offer:
- Catering
- Rent-A-Chef Events
- Sushi Making Classes

For reference our chopsticks from the logo files we use on a lot of print items. Not that I want it to be like this, but I did attach a sample of what ChatGPT created though is in an unusable format and fonts aren't consistent. As well a recent 2' x 4' sign we had made to use on table displays.

We also do like the wording on that last item of " Sushi | Experience | Elevated"

```html
<!DOCTYPE html>
<html lang="en">
<head>
<meta charset="utf-8">
<title>Kelp Corner – Trailer Lettering</title>
<link href="https://fonts.googleapis.com/css2?family=Saira+Condensed:wght@300;400;500&display=swap" rel="stylesheet">
<style>
  :root {
    --canvas: #9c9c9c;
    --panel: #000000;
    --red: #d4161c;
    --red-line: #8e1016;
    --white: #ffffff;
    --frame: #c9c9c9;
    --frame-shade: #8d8d8d;
  }
  html, body {
    margin: 0;
    padding: 0;
    width: 1063px;
    height: 1200px;
    overflow: hidden;
    background: var(--canvas);
  }
  .canvas {
    position: relative;
    width: 1063px;
    height: 1200px;
    font-family: "Saira Condensed", "Arial Narrow", sans-serif;
  }
  .panel {
    position: absolute;
    top: 394px;
    height: 412px;
    background: var(--panel);
  }
  .panel--front { left: 41px; width: 202px; }
  .panel--side  { left: 266px; width: 755px; }
  .panel svg { display: block; width: 100%; height: 100%; }

  .brand-name { fill: var(--white); font-weight: 400; }
  .icon-ring { fill: none; stroke: var(--red); stroke-width: 2.4; }
  .icon-glyph { color: var(--white); }
  .rule { stroke: var(--red-line); stroke-width: 1; }
  .txt { fill: var(--white); font-weight: 300; }
  .txt--label { fill: var(--red); font-weight: 300; }
  .tagline { fill: var(--white); font-weight: 400; }
  .tag-bar { fill: var(--red); }
  .web-band { fill: var(--red); }
  .web-text { fill: var(--panel); font-weight: 400; }
  .contact-ring { fill: none; stroke: var(--red); stroke-width: 1.6; }
  .door-frame { fill: none; stroke: var(--frame); stroke-width: 7; }
  .door-edge { fill: none; stroke: var(--frame-shade); stroke-width: 1; }
</style>
</head>
<body>
<svg width="0" height="0" style="position:absolute" aria-hidden="true">
  <defs>
    <symbol id="icon-cloche" viewBox="0 0 24 24">
      <g fill="none" stroke="currentColor" stroke-width="1.6" stroke-linecap="round">
        <path d="M5 16a7 7 0 0 1 14 0z"/>
        <line x1="3" y1="18" x2="21" y2="18"/>
        <line x1="12" y1="7" x2="12" y2="9"/>
      </g>
    </symbol>
    <symbol id="icon-chef" viewBox="0 0 24 24">
      <g fill="none" stroke="currentColor" stroke-width="1.6" stroke-linejoin="round">
        <path d="M7 14c-2.5-.5-3.5-4-1-5.5.3-2.5 3.5-3.8 5.3-2 1.6-2 5-1 5.2 1.3 2.8.6 2.8 5 .5 6.2v5H7z"/>
        <line x1="7" y1="16" x2="17" y2="16"/>
      </g>
    </symbol>
    <symbol id="icon-rolls" viewBox="0 0 24 24">
      <g fill="none" stroke="currentColor" stroke-width="1.5">
        <ellipse cx="8" cy="10" rx="4.5" ry="2"/>
        <path d="M3.5 10v5c0 1.1 2 2 4.5 2s4.5-.9 4.5-2v-5"/>
        <ellipse cx="16" cy="8" rx="4.5" ry="2"/>
        <path d="M20.5 8v5c0 1.1-2 2-4.5 2"/>
      </g>
    </symbol>
    <symbol id="icon-phone" viewBox="0 0 24 24">
      <path d="M7 4l3 4-2 2c1 2.5 3.5 5 6 6l2-2 4 3-2 3C10 20 4 14 4 6z" fill="none" stroke="currentColor" stroke-width="1.6" stroke-linejoin="round"/>
    </symbol>
    <symbol id="icon-mail" viewBox="0 0 24 24">
      <g fill="none" stroke="currentColor" stroke-width="1.6">
        <rect x="4" y="7" width="16" height="11"/>
        <path d="M4 7l8 6 8-6"/>
      </g>
    </symbol>
  </defs>
</svg>

<main class="canvas">

  <!-- Front panel -->
  <section class="panel panel--front" aria-label="Front panel">
    <svg viewBox="0 0 202 412">
      <g class="brand-name-block">
        <text class="brand-name" x="100" y="64" font-size="32" text-anchor="middle">kelp</text>
        <text class="brand-name" x="100" y="95" font-size="32" text-anchor="middle">corner</text>
      </g>

      <g class="contact">
        <circle class="contact-ring" cx="33" cy="153" r="5.5"/>
        <use href="#icon-phone" x="29" y="149" width="8" height="8" class="icon-glyph"/>
        <text class="txt" x="43" y="162" font-size="25" font-weight="400">(405) 555-2716</text>

        <circle class="contact-ring" cx="33" cy="184" r="5.5"/>
        <use href="#icon-mail" x="29" y="180" width="8" height="8" class="icon-glyph"/>
        <text class="txt" x="45" y="189" font-size="12.5">catering@kelpcornerok.com</text>

        <path class="web-band" d="M25 204 L175 203 L178 207 L175 217 L26 218 L22 213 Z"/>
        <text class="web-text" x="100" y="215" font-size="12.5" text-anchor="middle">www.kelpcornerok.com</text>
      </g>

      <line class="rule" x1="17" y1="237" x2="183" y2="237"/>

      <g class="services">
        <circle class="icon-ring" cx="44" cy="271" r="16"/>
        <use href="#icon-cloche" x="35" y="262" width="18" height="18" class="icon-glyph"/>
        <text class="txt" x="44" y="303" font-size="10.5" text-anchor="middle">catering</text>

        <circle class="icon-ring" cx="101" cy="271" r="16"/>
        <use href="#icon-chef" x="92" y="262" width="18" height="18" class="icon-glyph"/>
        <text class="txt" x="101" y="303" font-size="10.5" text-anchor="middle">rent-a-chef</text>
        <text class="txt" x="101" y="313" font-size="10.5" text-anchor="middle">events</text>

        <circle class="icon-ring" cx="160" cy="271" r="16"/>
        <use href="#icon-rolls" x="151" y="262" width="18" height="18" class="icon-glyph"/>
        <text class="txt" x="160" y="303" font-size="10.5" text-anchor="middle">sushi making</text>
        <text class="txt" x="160" y="313" font-size="10.5" text-anchor="middle">classes</text>
      </g>
    </svg>
  </section>

  <!-- Side panel -->
  <section class="panel panel--side" aria-label="Side panel">
    <svg viewBox="0 0 755 412">
      <g class="brand-name-block">
        <text class="brand-name" x="118" y="118" font-size="54" text-anchor="middle">kelp</text>
        <text class="brand-name" x="118" y="168" font-size="54" text-anchor="middle">corner</text>
      </g>

      <g class="services">
        <circle class="icon-ring" cx="260" cy="69" r="18"/>
        <use href="#icon-cloche" x="250" y="59" width="20" height="20" class="icon-glyph"/>
        <text class="txt" x="290" y="73" font-size="11.5">catering</text>

        <line class="rule" x1="244" y1="96" x2="342" y2="96"/>

        <circle class="icon-ring" cx="260" cy="127" r="18"/>
        <use href="#icon-chef" x="250" y="117" width="20" height="20" class="icon-glyph"/>
        <text class="txt" x="290" y="124" font-size="11.5">rent-a-chef</text>
        <text class="txt" x="290" y="135" font-size="11.5">events</text>

        <line class="rule" x1="244" y1="154" x2="342" y2="154"/>

        <circle class="icon-ring" cx="260" cy="184" r="18"/>
        <use href="#icon-rolls" x="250" y="174" width="20" height="20" class="icon-glyph"/>
        <text class="txt" x="290" y="181" font-size="11.5">sushi making</text>
        <text class="txt" x="290" y="193" font-size="11.5">classes</text>
      </g>

      <g class="tagline-group">
        <rect class="tag-bar" x="380" y="79" width="2" height="25"/>
        <text class="tagline" x="391" y="100" font-size="27">sushi</text>
        <rect class="tag-bar" x="380" y="114" width="2" height="25"/>
        <text class="tagline" x="391" y="135" font-size="27">experience</text>
        <rect class="tag-bar" x="380" y="149" width="2" height="25"/>
        <text class="tagline" x="391" y="169" font-size="27">elevated</text>
      </g>

      <line class="rule" x1="38" y1="237" x2="494" y2="237"/>

      <g class="locations">
        <text class="txt--label" x="38" y="272" font-size="12.5">Edmond</text>
        <text class="txt" x="38" y="290" font-size="12.5">4875 NE 92nd,</text>
        <text class="txt" x="38" y="306" font-size="12.5">Edmond, OK 73099</text>

        <text class="txt--label" x="146" y="273" font-size="12.5">NW-OKC</text>
        <text class="txt" x="146" y="291" font-size="12.5">2719 E Larkspur Ave,</text>
        <text class="txt" x="146" y="307" font-size="12.5">Oklahoma City, OK 73198</text>
      </g>

      <g class="contact">
        <circle class="contact-ring" cx="290" cy="267" r="8"/>
        <use href="#icon-phone" x="284" y="261" width="12" height="12" class="icon-glyph"/>
        <text class="txt" x="307" y="274" font-size="20" font-weight="400">(405) 555-2716</text>

        <circle class="contact-ring" cx="290" cy="300" r="8"/>
        <use href="#icon-mail" x="284" y="294" width="12" height="12" class="icon-glyph"/>
        <text class="txt" x="307" y="307" font-size="20" font-weight="400">catering@kelpcornerok.com</text>

        <path class="web-band" d="M255 331 L503 328 L507 334 L503 350 L258 352 L252 342 Z"/>
        <text class="web-text" x="380" y="347" font-size="20" text-anchor="middle">www.kelpcornerok.com</text>
      </g>

      <g class="door">
        <rect class="door-frame" x="527" y="67" width="159" height="321"/>
        <rect class="door-edge" x="523" y="63" width="167" height="329"/>
        <rect class="door-edge" x="531" y="71" width="151" height="313"/>
        <text class="brand-name" x="607" y="220" font-size="34" text-anchor="middle">kelp</text>
        <text class="brand-name" x="607" y="252" font-size="34" text-anchor="middle">corner</text>
      </g>
    </svg>
  </section>

</main>
</body>
</html>
```